New Business Card Design for Houston-based Office Building Association

We need a business card design for our membership association in Houston known at Houston PELQ (Houston Tower Keepers & Stewards Guild). Our members are office building managers and vendors in the commercial real estate industry. Any building imagery should be of office buildings, skyscrapers, skylines, etc. (Please do NOT use houses or residential homes.) The final design should be clean and cohesive utilizing our logo and branding. I've attached our logos, branding guide, and the information to be included on the business cards.

Target Market(s)

Professionals in office buildings and commercial real estate. Our market is conservative, modern and upmarket.

Contact Information for Business Card

Should include: name, title, email, direct phone number, cell phone number, address, and possibly website. Our address is 4 Larkmoor Court, Suite 300, Houston TX 77021. Our website is houstonpelq.org. Other fields should be editable for each employee.

Colors
ffffff
33b8a4
86cfc6
00a990

Requirements
Must have
• Clean, professional, modern, look, integrating our branding, logo and colors. Our logo font is Gotham Light and signature color is PMS color Pantone 2401C (hex code 40a89d.) Our accent color is PMS color Pantone Cool Gray 10C (hex code: 636466)
Should not have
• NO imagery of homes or residential houses. We represent commercial real estate/office buildings only.

```html
<!DOCTYPE html>
<html lang="en">
<head>
<meta charset="utf-8">
<title>Houston PELQ — Business Card</title>
<link href="https://fonts.googleapis.com/css2?family=Montserrat:wght@300;400&display=swap" rel="stylesheet">
<style>
  :root {
    --brand-teal: #36a89d;
    --accent-teal: #2fa596;
    --ink-gray: #636466;
    --paper: #ffffff;
    --stage: #e9ebea;
    --card-shadow: rgba(0, 0, 0, 0.18);
  }
  * { margin: 0; padding: 0; box-sizing: border-box; }
  html, body {
    width: 1200px; height: 780px; overflow: hidden;
    background: var(--stage);
    font-family: "Montserrat", Arial, sans-serif;
    font-weight: 300;
  }
  .stage {
    position: relative; width: 1200px; height: 780px;
    display: flex; align-items: center; justify-content: center; gap: 40px;
  }
  .card {
    position: relative; width: 540px; height: 309px;
    border-radius: 22px; overflow: hidden;
    box-shadow: 0 10px 28px var(--card-shadow);
  }

  /* Front */
  .card--front {
    background: var(--brand-teal);
    display: flex; align-items: center; justify-content: center;
  }
  .front-name {
    display: flex; align-items: center; gap: 14px;
  }
  .front-name .name-square {
    width: 18px; height: 18px; background: var(--paper);
  }
  .front-name .org-name {
    color: var(--paper); font-weight: 400; font-size: 28px;
    letter-spacing: 0.5px;
  }

  /* Back */
  .card--back { background: var(--paper); }
  .back-name {
    position: absolute; right: 36px; top: 40px;
    display: flex; align-items: center; gap: 10px;
  }
  .back-name .name-square {
    width: 12px; height: 12px; background: var(--brand-teal);
  }
  .back-name .org-name {
    color: var(--brand-teal); font-size: 18px; font-weight: 400;
    letter-spacing: 0.3px;
  }
  .person {
    position: absolute; left: 36px; top: 140px;
  }
  .person .name {
    color: var(--ink-gray); font-size: 17px; font-weight: 400;
    text-transform: uppercase; letter-spacing: 0.5px;
  }
  .person .title {
    color: var(--brand-teal); font-size: 13px; margin-top: 2px;
  }
  .rule {
    position: absolute; left: 36px; right: 36px; top: 192px;
    height: 1px; background: var(--brand-teal);
  }
  .contact {
    position: absolute; left: 36px; right: 20px; top: 204px;
    color: var(--ink-gray); font-size: 11.5px; line-height: 20px;
  }
  .contact .label { color: var(--accent-teal); }
  .contact .web { color: var(--accent-teal); }
</style>
</head>
<body>
<main class="stage">
  <section class="card card--front" aria-label="Card front">
    <div class="front-name">
      <div class="name-square"></div>
      <div class="org-name">Houston PELQ</div>
    </div>
  </section>

  <section class="card card--back" aria-label="Card back">
    <div class="back-name">
      <div class="name-square"></div>
      <div class="org-name">Houston PELQ</div>
    </div>
    <div class="person">
      <div class="name">Dana Mercer</div>
      <div class="title">Owner</div>
    </div>
    <div class="rule"></div>
    <div class="contact">
      <div><span class="label">Cell:</span> (555) 210-4478 | <span class="label">Office:</span> (555) 210-4478 | <span class="label">Email:</span> hello@pelqmail.com</div>
      <div><span class="label">Address:</span> 4 Larkmoor Court, Suite 300, Houston TX 77021</div>
      <div class="web">houstonpelq.org</div>
    </div>
  </section>
</main>
</body>
</html>
```